Dental Practice Website design

Design a new website for Brambleford Dental Practice.
Design should be warm, neutral in colour, with some small amount of bright colour if needed but kept to a minimum. Website should look professional, high end. Home page should be easy to navigate and simple for patients to be able to book online.
Logo in files along with some examples of websites that we like. Please ask if any further info needed.
Menu should have:
About
New Patients
Treatments
Fees
Contact Us

Industry/Entity Type

Dentistry

Number of Pages Required

4 page

Font styles to use
Sans Serif

Colors

Designer to choose colors to be used in the design.

Requirements
Must have
• Ravelle ratings badge, book online button,
Nice to have
• neutral, relaxing colours
Should not have
• harsh, bright colours!

```html
<!DOCTYPE html>
<html lang="en">
<head>
<meta charset="utf-8">
<title>Brambleford Dental Practice</title>
<link rel="stylesheet" href="https://fonts.googleapis.com/css2?family=Barlow:wght@300;400;500;600;700&family=Barlow+Condensed:wght@500;600&family=Exo+2:wght@300;400;700&display=swap">
<style>
:root{
  --ink:#13222a;
  --ink-soft:#1c2f38;
  --sky:#e0f5f8;
  --sky-mid:#cfe7eb;
  --teal:#4c93a8;
  --teal-deep:#2f6f84;
  --sage:#9fc7cd;
  --mint:#a9d6dc;
  --white:#ffffff;
  --text:#1b2a31;
  --muted:#5f7a84;
  --star:#e7b32d;
}
*{box-sizing:border-box;margin:0;padding:0}
html,body{width:1200px;height:4878px;overflow:hidden}
body{position:relative;background:var(--sky);font-family:"Barlow",sans-serif;color:var(--text)}
.abs{position:absolute}
.heading{font-family:"Exo 2",sans-serif;font-weight:300;letter-spacing:.5px}
.heading b{font-weight:700}
.btn{position:absolute;display:flex;align-items:center;justify-content:center;border-radius:8px;font-family:"Barlow",sans-serif;font-weight:600;font-size:14px;letter-spacing:.3px;text-transform:uppercase;text-decoration:none}
.btn-light{background:var(--white);color:var(--ink)}
.btn-dark{background:var(--ink);color:var(--white)}
.photo{position:absolute}

/* header */
.site-header{position:absolute;left:0;top:0;width:1200px;height:113px;background:var(--ink);z-index:2}
.brand{position:absolute;left:140px;top:30px;color:#c9d4d8;font-family:"Barlow",sans-serif;font-weight:300;line-height:1}
.brand .brand-name{font-size:30px;letter-spacing:1px}
.brand .brand-sub{font-size:13px;letter-spacing:1.5px;margin-top:4px}
.main-nav{position:absolute;top:48px;left:418px;display:flex;gap:29px;color:#d7e3e6;font-size:14px}
.main-nav .active{position:relative}
.main-nav .active::after{content:"";position:absolute;left:-10px;right:-10px;top:54px;height:2px;background:#cfe2e6}

/* hero */
.hero{position:absolute;left:0;top:113px;width:1200px;height:607px;background:linear-gradient(100deg,#5aa6bb 0%,#3f8aa0 55%,#2f7389 100%);overflow:hidden}
.hero-photo{position:absolute;left:0;top:0;width:660px;height:607px;
  background:
   radial-gradient(ellipse 150px 190px at 50% 32%,rgba(196,146,112,.85) 0%,rgba(150,104,80,.55) 55%,rgba(150,104,80,0) 100%),
   radial-gradient(ellipse 230px 230px at 46% 30%,rgba(40,30,28,.75) 0%,rgba(40,30,28,.35) 60%,rgba(40,30,28,0) 100%),
   radial-gradient(ellipse 330px 200px at 48% 92%,rgba(86,170,196,.95) 0%,rgba(86,170,196,.5) 60%,rgba(86,170,196,0) 100%),
   linear-gradient(100deg,#5fa9bd 0%,#4c98ae 70%,rgba(76,152,174,0) 100%)}
.hero-tag{position:absolute;left:668px;top:208px;background:var(--ink);color:#fff;font-size:20px;padding:3px 22px 4px 16px;clip-path:polygon(0 0,100% 0,92% 100%,0 100%);z-index:1}
.hero-title{position:absolute;left:668px;top:250px;font-family:"Barlow Condensed",sans-serif;font-weight:600;font-size:62px;line-height:72px;color:#fff;letter-spacing:1px;z-index:1}
.hero-arrow{position:absolute;top:565px;width:30px;height:30px;border-radius:50%;background:rgba(255,255,255,.35);display:flex;align-items:center;justify-content:center;z-index:1}

/* about */
.about-text{position:absolute;left:142px;top:882px;width:450px;font-size:12.5px;line-height:19.5px;color:#1e2c33}
.about-text p{margin-bottom:19px}

/* services */
.service-card{position:absolute;width:453px;height:318px;border-radius:18px;overflow:hidden}
.service-card .shade{position:absolute;inset:0;background:linear-gradient(180deg,rgba(19,34,42,0) 38%,rgba(19,34,42,.55) 62%,rgba(19,34,42,.95) 88%)}
.service-card .icon{position:absolute;left:48px;top:135px;width:76px;height:76px;border-radius:50%;border:1.5px solid rgba(255,255,255,.75);background:rgba(255,255,255,.14);display:flex;align-items:center;justify-content:center}
.service-card h3{position:absolute;left:48px;top:220px;font-family:"Exo 2",sans-serif;font-weight:300;font-size:40px;color:#fff;letter-spacing:.5px}
.service-card p{position:absolute;left:49px;top:275px;width:370px;font-size:14px;line-height:18px;color:#e6eef0}

/* team */
.team-card{position:absolute;top:3212px;width:277px;height:413px;border-radius:6px;overflow:hidden}
.team-card .shade{position:absolute;inset:0;background:linear-gradient(180deg,rgba(19,34,42,0) 50%,rgba(19,34,42,.92) 100%)}
.team-card .name{position:absolute;left:45px;top:295px;font-family:"Exo 2",sans-serif;font-weight:300;font-size:26px;color:#fff}
.team-card .role{position:absolute;left:45px;top:332px;font-size:11px;color:#d8e3e6}

/* reviews */
.review-card{position:absolute;top:3816px;width:288px;height:188px;background:var(--sky);border-radius:4px;padding:30px 18px 0 18px}
.review-card .stars{color:var(--star);font-size:14px;letter-spacing:1px}
.review-card p{font-size:12.5px;line-height:19px;margin-top:6px;color:#1e2c33}
.review-card .badge{position:absolute;right:22px;bottom:18px;width:24px;height:24px;border-radius:50%;background:var(--teal-deep)}

/* contact */
.contact-form{position:absolute;left:148px;top:4165px;width:372px;height:560px;background:var(--ink);border-radius:18px 18px 0 0}
.field{position:absolute;left:30px;width:312px;border-bottom:1px solid #5a6c74;height:26px;font-size:12px;color:#9aaab0}
.address{position:absolute;left:572px;top:4190px}
.address li{list-style:none;display:flex;gap:10px;font-size:12.5px;line-height:24px}
.social{position:absolute;top:4400px;width:36px;height:36px;border-radius:50%;border:1.5px dashed #4e6670}

/* footer */
.footer-nav{position:absolute;top:4746px;left:520px;display:flex;gap:30px;color:#d7e3e6;font-size:14px}
</style>
</head>
<body>

<header class="site-header">
  <div class="brand">
    <div class="brand-name">BRAMBLEFORD</div>
    <div class="brand-sub">DENTAL PRACTICE</div>
  </div>
  <nav class="main-nav">
    <span class="active">About</span><span>New Patients</span><span>Treatments</span><span>Fees</span><span>Contact Us</span>
  </nav>
  <a class="btn btn-light" style="left:868px;top:33px;width:207px;height:45px">Book an Appointment</a>
</header>

<section class="hero">
  <div class="hero-photo" role="img" aria-label="Smiling woman with curly dark hair in a teal top"></div>
</section>
<div class="hero-tag">Welcome To</div>
<div class="hero-title">BRAMBLEFORD<br>DENTAL<br>PRACTICE</div>
<a class="btn btn-light" style="left:668px;top:486px;width:205px;height:45px;z-index:1">Book an Appointment</a>
<div class="hero-arrow" style="left:672px"><svg width="10" height="10" viewBox="0 0 10 10"><path d="M6.5 1.5 3 5l3.5 3.5" fill="none" stroke="#fff" stroke-width="1.6"/></svg></div>
<div class="hero-arrow" style="left:734px"><svg width="10" height="10" viewBox="0 0 10 10"><path d="M3.5 1.5 7 5 3.5 8.5" fill="none" stroke="#fff" stroke-width="1.6"/></svg></div>
<svg class="abs" style="left:0;top:560px" width="1200" height="162" viewBox="0 0 1200 162">
  <path d="M0 80 Q600 230 1200 40 L1200 162 L0 162Z" fill="var(--ink)"/>
  <path d="M0 40 Q420 200 1200 162 L0 162Z" fill="var(--sky)"/>
</svg>

<!-- about -->
<h2 class="abs heading" style="left:142px;top:800px;font-size:58px;color:var(--ink);border-left:4px solid var(--ink);padding-left:14px;line-height:60px"><b>About</b> Us</h2>
<div class="about-text">
  <p>Welcome to our friendly dental practice nestled in the heart of beautiful Fernhollow, UK. Our team of dedicated dentists, hygienists and support staff are here to provide you with exceptional dental care. With a wide array of services, including general and cosmetic dentistry, orthodontics and emergency care, we're confident that we can deliver the highest quality treatment to you and your loved ones.</p>
  <p>At our practice, we believe that a visit to the dentist should be a comfortable and positive experience. We strive to create a warm and welcoming atmosphere where our patients can feel at ease and confident in the care they receive. Our state-of-the-art facilities and equipment mean that you can trust us to deliver the latest techniques and treatments to ensure your oral health is at its best.</p>
  <p>We are passionate about improving dental health and helping you achieve your brightest smile and are honoured that you're considering us for your dental needs. Please don't hesitate to contact us if you have any questions or to <b>schedule an appointment</b>. We look forward to welcoming you to our practice.</p>
</div>
<a class="btn btn-dark" style="left:142px;top:1267px;width:126px;height:44px">Learn More</a>
<div class="photo" role="img" aria-label="Smiling blonde patient in a bright dental clinic" style="left:630px;top:797px;width:436px;height:436px;border-radius:50%;border:8px solid var(--ink);background:
  radial-gradient(ellipse 110px 140px at 66% 40%,rgba(232,196,160,.95) 0%,rgba(214,178,130,.6) 60%,rgba(214,178,130,0) 100%),
  radial-gradient(ellipse 90px 120px at 22% 28%,rgba(245,248,250,.95) 0%,rgba(245,248,250,0) 100%),
  radial-gradient(ellipse 200px 120px at 62% 92%,rgba(240,244,246,.95) 0%,rgba(240,244,246,0) 100%),
  linear-gradient(160deg,#eef4f7 0%,#cfe1ea 50%,#8fb8c9 100%)"></div>
<div class="photo" role="img" aria-label="Portrait of a smiling dentist with dark hair" style="left:612px;top:1095px;width:250px;height:250px;border-radius:50%;border:10px solid var(--mint);background:
  radial-gradient(ellipse 55px 70px at 50% 42%,rgba(214,160,128,.95) 0%,rgba(190,130,100,.6) 60%,rgba(190,130,100,0) 100%),
  radial-gradient(ellipse 120px 80px at 50% 100%,rgba(150,30,90,.95) 0%,rgba(150,30,90,0) 100%),
  linear-gradient(180deg,#5a3a2e 0%,#3e2822 60%,#2e1f1c 100%)"></div>

<!-- services -->
<svg class="abs" style="left:0;top:1383px" width="1200" height="1065" viewBox="0 0 1200 1065">
  <path d="M0 0H1200V900 Q600 1180 0 900Z" fill="var(--ink)"/>
</svg>
<h2 class="abs heading" style="left:0;width:1200px;text-align:center;top:1452px;font-size:60px;color:#fff"><b>Our</b> Services</h2>
<article class="service-card" style="left:136px;top:1575px">
  <div class="photo" role="img" aria-label="Smiling couple" style="inset:0;background:
    radial-gradient(ellipse 90px 110px at 30% 40%,rgba(220,180,150,.9) 0%,rgba(220,180,150,0) 100%),
    radial-gradient(ellipse 100px 120px at 72% 35%,rgba(200,150,120,.9) 0%,rgba(200,150,120,0) 100%),
    linear-gradient(120deg,#8aa1a8,#9e8c80 50%,#5c7580)"></div>
  <div class="shade"></div>
  <div class="icon"><svg width="34" height="36" viewBox="0 0 34 36"><path d="M9 3c3 0 5 2 8 2s5-2 8-2c5 0 7 4 7 9 0 6-3 9-4 16-.5 4-2 6-3.5 6S22 32 21 27c-.6-3-2-5-4-5s-3.4 2-4 5c-1 5-2 7-3.5 7S7 32 6.5 28C5.5 21 2 18 2 12c0-5 2-9 7-9Z" fill="none" stroke="#fff" stroke-width="1.6"/></svg></div>
  <h3>General Dentistry</h3><p>Lorem ipsum dolor sit amet, consectetur adipiscing elit, sed do eiusmod tempor.</p>
</article>
<article class="service-card" style="left:610px;top:1575px">
  <div class="photo" role="img" aria-label="Group of smiling women" style="inset:0;background:
    radial-gradient(ellipse 60px 80px at 14% 40%,rgba(210,160,125,.9) 0%,rgba(210,160,125,0) 100%),
    radial-gradient(ellipse 60px 80px at 40% 38%,rgba(225,180,145,.9) 0%,rgba(225,180,145,0) 100%),
    radial-gradient(ellipse 60px 80px at 64% 40%,rgba(140,90,65,.9) 0%,rgba(140,90,65,0) 100%),
    radial-gradient(ellipse 60px 80px at 88% 42%,rgba(110,70,52,.9) 0%,rgba(110,70,52,0) 100%),
    linear-gradient(120deg,#5e4538,#8a6a55 50%,#3d2f2a)"></div>
  <div class="shade"></div>
  <div class="icon"><svg width="34" height="34" viewBox="0 0 34 34"><path d="M17 4l2.6 8.4L28 15l-8.4 2.6L17 26l-2.6-8.4L6 15l8.4-2.6Z" fill="none" stroke="#fff" stroke-width="1.6"/><circle cx="27" cy="6" r="2" fill="none" stroke="#fff" stroke-width="1.3"/></svg></div>
  <h3>Cosmetic Dentistry</h3><p>Lorem ipsum dolor sit amet, consectetur adipiscing elit, sed do eiusmod tempor.</p>
</article>
<article class="service-card" style="left:136px;top:1935px">
  <div class="photo" role="img" aria-label="Close-up smile with clear aligner" style="inset:0;background:
    radial-gradient(ellipse 180px 50px at 60% 28%,rgba(250,248,245,.95) 0%,rgba(250,248,245,0) 100%),
    radial-gradient(ellipse 240px 110px at 60% 30%,rgba(190,110,100,.85) 0%,rgba(190,110,100,0) 100%),
    linear-gradient(160deg,#d2a892,#e5cfc2 45%,#7a564c)"></div>
  <div class="shade"></div>
  <div class="icon"><svg width="38" height="26" viewBox="0 0 38 26"><rect x="3" y="4" width="32" height="18" rx="6" fill="none" stroke="#fff" stroke-width="1.6"/><path d="M3 13h32M12 4v18M19 4v18M26 4v18" stroke="#fff" stroke-width="1.3"/></svg></div>
  <h3>Orthodontics</h3><p>Lorem ipsum dolor sit amet, consectetur adipiscing elit, sed do eiusmod tempor.</p>
</article>
<article class="service-card" style="left:610px;top:1935px">
  <div class="photo" role="img" aria-label="Glowing digital render of teeth" style="inset:0;background:
    radial-gradient(ellipse 160px 90px at 55% 35%,rgba(120,170,255,.85) 0%,rgba(120,170,255,0) 100%),
    radial-gradient(ellipse 90px 60px at 80% 45%,rgba(230,120,80,.6) 0%,rgba(230,120,80,0) 100%),
    linear-gradient(140deg,#1c3680,#3f5fc0 45%,#141d48)"></div>
  <div class="shade"></div>
  <div class="icon"><svg width="30" height="30" viewBox="0 0 30 30"><path d="M11 3h8v8h8v8h-8v8h-8v-8H3v-8h8Z" fill="none" stroke="#fff" stroke-width="1.6"/></svg></div>
  <h3>Emergency care</h3><p>Lorem ipsum dolor sit amet, consectetur adipiscing elit, sed do eiusmod tempor.</p>
</article>
<a class="btn btn-light" style="left:496px;top:2327px;width:207px;height:45px">Book an Appointment</a>

<!-- join -->
<div class="photo" role="img" aria-label="Faded dental clinic interior" style="left:0;top:2450px;width:1200px;height:640px;z-index:-1;background:
  radial-gradient(ellipse 300px 200px at 82% 60%,rgba(240,250,252,.9) 0%,rgba(240,250,252,0) 100%),
  radial-gradient(ellipse 260px 180px at 40% 20%,rgba(190,222,228,.9) 0%,rgba(190,222,228,0) 100%),
  linear-gradient(180deg,#d7eef1,#c9e3e7)"></div>
<div class="photo" role="img" aria-label="Dental chair and treatment equipment" style="left:174px;top:2525px;width:354px;height:447px;border-radius:6px;background:
  radial-gradient(ellipse 120px 160px at 40% 62%,rgba(215,238,242,.95) 0%,rgba(215,238,242,0) 100%),
  radial-gradient(ellipse 80px 60px at 78% 50%,rgba(235,246,248,.9) 0%,rgba(235,246,248,0) 100%),
  linear-gradient(160deg,#a9d3da,#7fb8c0 60%,#5f9ea8)"></div>
<h2 class="abs heading" style="left:568px;top:2612px;font-size:60px;color:var(--ink)"><b>Join</b> Our Practice</h2>
<p class="abs" style="left:570px;top:2710px;width:450px;text-align:center;font-size:19.5px;line-height:25px;color:#1e2c33">If you're looking for an exceptional dental practice, we're here to help! Our team is made up of highly skilled professionals who are dedicated to ensuring that all our patients receive top-notch care in a welcoming and comfortable environment.</p>
<svg class="abs" style="left:760px;top:2868px" width="70" height="12"><circle cx="6" cy="6" r="5" fill="var(--ink)"/><circle cx="32" cy="6" r="5" fill="#aac5ca"/><circle cx="58" cy="6" r="5" fill="#aac5ca"/></svg>

<!-- team -->
<svg class="abs" style="left:0;top:3040px" width="1200" height="672" viewBox="0 0 1200 672">
  <path d="M0 160 Q600 -150 1200 160 V672 H0Z" fill="var(--ink)"/>
</svg>
<h2 class="abs heading" style="left:138px;top:3205px;font-size:60px;color:#fff"><b>Our</b> Team</h2>
<div class="abs" style="left:138px;top:3305px;width:340px;font-size:12.5px;line-height:19.5px;color:#e3ecee">
  <p style="margin-bottom:19px">We are delighted to introduce you to our experienced and compassionate dental team. Our team comprises highly skilled dental professionals who are dedicated to providing you with high-quality dental care services. Led by our experienced dentist, each member of our team brings their own unique set of skills and expertise.</p>
  <p>From our friendly reception staff to our knowledgeable hygienists and assistants, our team is here to ensure that you receive personalised dental care that meets your unique needs and preferences. We take great pride in providing a safe, comfortable, and welcoming environment for our patients, and we look forward to serving you with the utmost care and attention.</p>
</div>
<article class="team-card" style="left:522px">
  <div class="photo" role="img" aria-label="Male dentist in a white coat" style="inset:0;background:
    radial-gradient(ellipse 70px 90px at 50% 30%,rgba(205,160,130,.9) 0%,rgba(205,160,130,0) 100%),
    radial-gradient(ellipse 120px 110px at 50% 85%,rgba(225,230,235,.85) 0%,rgba(225,230,235,0) 100%),
    linear-gradient(180deg,#3a4a54,#4a5a64 50%,#2a3a42)"></div>
  <div class="shade"></div><div class="name">Alden</div><div class="role">Senior Doctor</div>
</article>
<article class="team-card" style="left:837px">
  <div class="photo" role="img" aria-label="Female dentist portrait" style="inset:0;background:
    radial-gradient(ellipse 65px 85px at 50% 32%,rgba(220,175,145,.9) 0%,rgba(220,175,145,0) 100%),
    radial-gradient(ellipse 110px 130px at 50% 38%,rgba(120,85,60,.8) 0%,rgba(120,85,60,0) 100%),
    linear-gradient(180deg,#d6d2ce,#b4aca6 50%,#4a5258)"></div>
  <div class="shade"></div><div class="name">Maris</div><div class="role">Senior Doctor</div>
</article>
<svg class="abs" style="left:792px;top:3628px" width="54" height="14"><path d="M6 3 2 7l4 4M48 3l4 4-4 4" fill="none" stroke="#fff" stroke-width="1.5"/></svg>

<!-- reviews -->
<section class="abs" style="left:0;top:3710px;width:1200px;height:372px;background:var(--sage)"></section>
<h2 class="abs heading" style="left:138px;top:3748px;font-size:34px;color:var(--ink)"><b>Ravelle</b> Reviews</h2>
<div class="review-card" style="left:136px"><div class="stars">★★★★★</div><p>Lorem ipsum dolor sit amet, consectetur adipiscing elit, sed do eiusmod tempor incididunt ut labore et dolore magna aliqua.</p><div class="badge" role="img" aria-label="Ravelle ratings badge"></div></div>
<div class="review-card" style="left:454px"><div class="stars">★★★★★</div><p>Lorem ipsum dolor sit amet, consectetur adipiscing elit, sed do eiusmod tempor incididunt ut labore et dolore magna aliqua.</p><div class="badge" role="img" aria-label="Ravelle ratings badge"></div></div>
<div class="review-card" style="left:770px"><div class="stars">★★★★★</div><p>Lorem ipsum dolor sit amet, consectetur adipiscing elit, sed do eiusmod tempor incididunt ut labore et dolore magna aliqua.</p><div class="badge" role="img" aria-label="Ravelle ratings badge"></div></div>

<!-- contact -->
<svg class="abs" style="left:0;top:4470px" width="1200" height="408" viewBox="0 0 1200 408">
  <path d="M0 180 Q500 -60 1200 20 V408 H0Z" fill="var(--ink)"/>
</svg>
<form class="contact-form">
  <h2 class="abs heading" style="left:0;width:372px;text-align:center;top:28px;font-size:34px;color:#fff">Contact</h2>
  <div class="field" style="top:125px">Name</div>
  <div class="field" style="top:197px">Email</div>
  <div class="field" style="top:277px">Phone</div>
  <div class="field" style="top:368px">Message</div>
  <div class="btn" style="left:34px;top:463px;width:180px;height:42px;background:var(--mint);color:var(--ink);text-transform:none;font-size:17px">Submit</div>
</form>
<div class="address">
  <h2 class="heading" style="font-size:34px;color:var(--ink);margin-bottom:16px">Address</h2>
  <ul>
    <li><svg width="12" height="14" viewBox="0 0 12 14" style="margin-top:5px"><path d="M6 13S1 7.8 1 5a5 5 0 0 1 10 0c0 2.8-5 8-5 8Z" fill="var(--ink)"/><circle cx="6" cy="5" r="1.8" fill="var(--sky)"/></svg><span>#123, lorium ipsum<br>Street Name.<br>City.</span></li>
    <li><svg width="12" height="12" viewBox="0 0 12 12" style="margin-top:6px"><path d="M2.5 1 4.5 3.5 3.3 5a7 7 0 0 0 3.7 3.7L8.5 7.5 11 9.5 9.8 11C5 11 1 7 1 2.2Z" fill="var(--ink)"/></svg><span>Ph: 1800 555 010 0199</span></li>
    <li><svg width="12" height="10" viewBox="0 0 12 10" style="margin-top:7px"><rect width="12" height="10" rx="1" fill="var(--ink)"/><path d="M1 1l5 4 5-4" fill="none" stroke="var(--sky)"/></svg><span>Mail : info@bramblefordpractice.com</span></li>
  </ul>
</div>
<div class="social" style="left:572px;background:var(--ink);border-style:solid" role="img" aria-label="Social link"></div>
<div class="social" style="left:622px" role="img" aria-label="Social link"></div>
<div class="social" style="left:672px" role="img" aria-label="Social link"></div>
<div class="social" style="left:722px" role="img" aria-label="Social link"></div>

<!-- footer -->
<div class="brand" style="left:184px;top:4752px">
  <div class="brand-name">BRAMBLEFORD</div>
  <div class="brand-sub">DENTAL PRACTICE</div>
</div>
<nav class="footer-nav"><span>Home</span><span>About Us</span><span>New Patients</span><span>Treatments</span><span>Fees</span><span>Contact Us</span></nav>
<p class="abs" style="left:770px;top:4791px;font-size:13px;color:#d7e3e6">© 2025 &nbsp;|&nbsp; www.bramblefordpractice.com</p>

</body>
</html>
```